OpenHarbor Yoga Website Design

Business Logo - attached
5 pages being:
Home
About
Classes
Blog
Contact

Would like Scrolling webpage and yoga symbols to be used.

Must have's being:
Easy to navigate, Text needs to be able to be edited/updated, Enquire Now Links, More Information Links, be a secure site, SEO,

Please refer to attached document for the information for the body of the website.

Target Market(s)

Educators, Community Service, Health and Wellbeing, Mental Health

Industry/Entity Type

Yoga

Coding

Coded - Design and coding required

Number of Pages Required

5+ page

Font styles to use
Other font styles liked:
• Bella Bold BC

Colors
0094D4
00A9DD
6FCCEA
C7EBF8
E9F6FB
6B429C
8869AF
B7A5CE
E3DAEB
F3F0F8

Requirements
Must have
• Easy to navigate, Text needs to be able to be edited/updated, Enquire Now Links, More Information Links, be a secure site, SEO,
Nice to have
• Scrolling webpage, yoga symbols

```html
<!DOCTYPE html>
<html lang="en">
<head>
<meta charset="utf-8">
<title>OpenHarbor Yoga – Website Design</title>
<link href="https://fonts.googleapis.com/css2?family=Kaushan+Script&family=Roboto:wght@400;700&family=Playfair+Display:wght@400;700&display=swap" rel="stylesheet">
<style>
:root{
  --board:#ad8ce0;
  --violet:#6b3fc0;
  --violet-deep:#5a35a8;
  --plum:#6b429c;
  --teal:#22c6da;
  --teal-deep:#1ba9c4;
  --sky:#6fccea;
  --lilac:#b7a5ce;
  --mist:#f3f0f8;
  --grey-band:#f2f2f4;
  --footer:#55408f;
  --ink:#4a4a55;
  --soft:#7a7a85;
}
*{box-sizing:border-box;margin:0;padding:0}
html,body{width:1037px;height:1200px;overflow:hidden}
body{background:var(--board);position:relative;font-family:'Roboto',sans-serif;color:var(--ink)}
ul{list-style:none}
.board-label{position:absolute;top:29px;transform:translateX(-50%);color:#fff;font-size:11px;white-space:nowrap}
.page{position:absolute;width:199px;background:#fff;overflow:hidden}
.page > *{position:absolute}
/* header */
.topbar{left:0;top:0;width:100%;height:9px;background:linear-gradient(90deg,#3a3c96,#1e9bb8 35%,#3f6cb0 60%,#6b3fa0);display:flex;justify-content:flex-end;align-items:center;gap:4px;padding-right:26px;font-size:2.4px;color:#fff}
.nav{left:0;top:9px;width:100%;height:17px;background:#fff}
.brand{position:absolute;left:18px;top:3px;display:flex;align-items:center;gap:1px;flex-direction:column}
.brand-dot{width:9px;height:9px;border-radius:50%;border:0.6px solid var(--lilac)}
.brand-name{font-size:1.8px;color:var(--plum);white-space:nowrap}
.nav-links{position:absolute;left:71px;top:7px;display:flex;gap:9px;font-family:'Playfair Display',serif;font-size:2.6px;color:#555}
.nav-links .on{color:var(--violet);border-bottom:0.6px solid var(--violet);padding-bottom:1.5px}
.pill{position:absolute;background:var(--violet);color:#fff;font-family:'Playfair Display',serif;font-size:2.5px;border-radius:5px;padding:1.6px 3px;white-space:nowrap}
.nav .pill{left:157px;top:4.5px}
.hero{left:0;top:26px;width:100%;height:96px;background:linear-gradient(180deg,#6a3ea6 0%,#3d86c4 60%,#22cbdc 100%)}
.hero.short{height:76px}
.hero-ring{position:absolute;left:22px;top:10px;width:74px;height:74px;border-radius:50%;border:1px solid rgba(200,180,255,.45)}
.hero.short .hero-ring{left:30px;top:6px;width:62px;height:62px}
.hero-title{position:absolute;left:96px;width:103px;top:34px;text-align:center;font-family:'Kaushan Script',cursive;font-size:11px;color:#fff;white-space:nowrap}
.hero.short .hero-title{top:30px;font-size:10px}
.hero .pill{background:#6b3fc0;border:0.6px solid #fff;left:135px;top:50px}
/* type */
.script{font-family:'Kaushan Script',cursive;color:var(--violet);white-space:nowrap}
.h-center{left:0;width:100%;text-align:center}
.txt{font-size:2.4px;line-height:1.4;color:var(--soft)}
.txt p+p{margin-top:1.6px}
.ticks li{font-size:2.4px;line-height:1.35;color:var(--soft);padding-left:4px;position:relative;margin-bottom:1.2px}
.ticks li::before{content:"";position:absolute;left:0;top:0.6px;border-left:1.2px solid transparent;border-right:1.2px solid transparent;border-bottom:2px solid var(--lilac)}
.ph{background:linear-gradient(135deg,#d9cbb8,#b9a894 55%,#8b8fa8)}
.ph.cool{background:linear-gradient(135deg,#c6d9e6,#9fb6cc 55%,#7a8fb0)}
.ph.warm{background:linear-gradient(135deg,#f0c98f,#d98a6e 50%,#7aa4c9)}
.ph.green{background:linear-gradient(160deg,#9fc58d,#d98b7a 55%,#6f9a5c)}
.frame{border:0.7px solid var(--lilac)}
.bar{background:var(--violet)}
/* footer */
.footer{left:0;width:100%;background:var(--footer);color:#fff}
.footer > *{position:absolute}
.f-title{font-family:'Kaushan Script',cursive;font-size:4.6px;top:8px}
.f-lines{top:15px;font-size:2.2px;line-height:1.6}
.f-logo{left:89px;top:9px;display:flex;flex-direction:column;align-items:center;gap:1px}
.f-logo .brand-dot{width:13px;height:13px;border-color:#cbbcf0}
.f-logo span.brand-name{color:#fff;font-size:1.9px}
.f-rule{left:20px;right:20px;top:45px;height:0.4px;background:rgba(255,255,255,.3)}
.f-copy{left:0;width:100%;top:51px;text-align:center;font-size:2.2px}
/* blog */
.blog-bg{left:0;top:102px;width:100%;background:var(--grey-band)}
.card{background:#fff;width:100px;height:69px;left:19px}
.card > *{position:absolute}
.card .thumb{left:5px;top:6px;width:29px;height:28px}
.card .c-title{left:38px;top:10px;width:58px;font-size:3.3px;font-weight:700;color:var(--violet-deep);line-height:1.15}
.card .c-meta{left:44px;top:27px;font-size:1.9px;color:#888}
.card .c-text{left:5px;top:39px;width:90px}
.card .avatar{left:6px;top:56px;width:9px;height:9px;border-radius:50%;background:#cfd2d8}
.card .c-author{left:17px;top:57px;font-size:1.9px;color:#999;line-height:1.3}
.card .c-author b{color:var(--violet-deep);font-weight:700;display:block}
.card .pill{left:65px;top:58px;background:var(--violet);font-size:1.9px}
.side{left:130px;width:50px}
.side > *{position:absolute}
.recent li{position:absolute;left:0;width:50px;display:flex;gap:2px}
.recent .rt{width:14px;height:12px;flex:none}
.recent .rx{font-size:1.7px;color:var(--violet-deep);font-weight:700;line-height:1.3}
.recent .rx em{display:block;font-style:normal;color:var(--teal-deep);margin-top:1px}
.ad{left:1px;width:48px;height:67px}
.ad-note{left:1px;width:48px;top:47px;height:20px;background:#6b2fc7;color:#fff;font-family:'Kaushan Script',cursive;font-size:2.6px;text-align:center;padding:3px 2px;line-height:1.2}
</style>
</head>
<body>

<div class="board-label" style="left:158px">Home Page</div>
<div class="board-label" style="left:398px">Classes Page Sample 2</div>
<div class="board-label" style="left:639px">Blog Page Sample 2</div>
<div class="board-label" style="left:879px">Single Blog Page Sample 2</div>
<div class="board-label" style="left:639px;top:693px">Contact Us Page</div>

<!-- HOME -->
<section class="page" style="left:59px;top:55px;height:729px">
  <div class="topbar"><span>✉ info@openharboryoga.com.au</span><span>☎ Call Us 0400 555 218</span></div>
  <nav class="nav"><div class="brand"><span class="brand-dot"></span><span class="brand-name">OpenHarbor Yoga</span></div>
    <ul class="nav-links"><li class="on">Home</li><li>About</li><li>Classes</li><li>Blog</li><li>Contact</li></ul><a class="pill">Enquire Now</a></nav>
  <header class="hero"><div class="hero-ring"></div><div class="hero-title" style="top:28px">OpenHarbor Yoga</div><a class="pill">Enquire Now</a></header>

  <h2 class="script h-center" style="top:134px;font-size:8.5px">Welcome to OpenHarbor Yoga...</h2>
  <div class="frame" style="left:15px;top:185px;width:36px;height:38px"></div>
  <div class="ph" role="img" aria-label="Photo of a person meditating cross-legged on a yoga mat" style="left:21px;top:155px;width:70px;height:64px"></div>
  <div class="txt" style="left:94px;top:155px;width:82px">
    <p>OpenHarbor Yoga believe that you are never too young to benefit from and fall in love with yoga. My aim is to empower kids and teens to thrive by teaching life skills in Yoga, Mindfulness and Breathing techniques to deal with daily challenges and big emotions.</p>
    <p>OpenHarbor Yoga gives kids an opportunity to enjoy and experience yoga for themselves and primarily focuses on programs for Schools, Pre Schools and Early Learning Centres, Private Classes, Sporting Clubs, Martial Arts Schools, Scout Groups and Occupational Therapy Centres just to name a few. All classes are age appropriate and encourage children's natural drive to learn, move, and be creative.</p>
  </div>
  <a class="pill" style="left:94px;top:211px">More Information</a>

  <div style="left:0;top:237px;width:199px;height:64px;background:linear-gradient(180deg,#26c2d8,#22b7d3)"></div>
  <h2 class="script h-center" style="top:243px;font-size:8.5px;color:#fff">Benefits of Yoga...</h2>
  <p class="txt" style="left:40px;width:119px;top:258px;text-align:center;color:#fff">The benefits of yoga can last a lifetime. It is my aim &amp; passion to introduce yoga to kids of all ages and backgrounds so that they can not only experience the benefits of yoga but fall in love with the practice.</p>
  <h3 class="script h-center" style="top:280px;font-size:5.5px;color:#fff">Yoga benefits include:</h3>

  <h3 class="script" style="left:21px;top:318px;font-size:7px">Healthy Bodies</h3>
  <ul class="ticks" style="left:21px;top:329px;width:72px"><li>Develops strong, flexible and healthy bodies</li><li>Promotes spinal alignment and good posture</li><li>Builds energy and stamina</li><li>Improves internal physical function - organs, digestion, elimination, circulation, and blood flow.</li><li>Helps breathing and lung capacity</li><li>Teaches the enjoyment of movement</li><li>Works the 'whole' body</li></ul>
  <div class="bar" style="left:101px;top:326px;width:81px;height:55px"></div>
  <div class="ph cool" role="img" aria-label="Photo of a group class holding a downward dog pose" style="left:97px;top:321px;width:81px;height:55px"></div>

  <div class="bar" style="left:11px;top:401px;width:82px;height:55px"></div>
  <div class="ph warm" role="img" aria-label="Photo of children sitting on mats with arms raised" style="left:15px;top:397px;width:82px;height:55px"></div>
  <h3 class="script" style="left:109px;top:401px;font-size:7px">Healthy Minds</h3>
  <ul class="ticks" style="left:109px;top:412px;width:80px"><li>Cultivates confidence and self-esteem</li><li>Develops concentration and attention</li><li>Clears the mind for better clarity and decision making</li><li>Helps relax and sleep better</li><li>Calms the nervous system</li><li>Learns to cope with stressful situations</li><li>Balances emotions</li></ul>

  <h3 class="script" style="left:21px;top:474px;font-size:7px">Healthy Spirits</h3>
  <ul class="ticks" style="left:21px;top:486px;width:72px"><li>Fosters creativity, expression and imagination</li><li>Cultivates kindness to themselves and others</li><li>Cultivates respect for self and others</li><li>Builds balance and inner quiet</li><li>Builds inner strength and resilience</li><li>Teaches self-awareness</li><li>Focuses on positive self-talk</li></ul>
  <div style="left:98px;top:481px;width:81px;height:56px;background:var(--teal-deep)"></div>
  <div class="ph" role="img" aria-label="Photo of adults stretching together in a studio" style="left:94px;top:476px;width:81px;height:56px"></div>

  <div class="txt" style="left:30px;width:139px;top:556px;text-align:center">
    <p>OpenHarbor Yoga combines all the benefits of traditional yoga and a lot of fun! We play games and practice engaging flows which get our bodies moving, then we take a quiet moment to be still and calm as we focus on our breathing.</p>
    <p>OpenHarbor Yoga Kids will learn that relaxation is just as important as moving their bodies, and the exercises which they learn in class can easily be repeated at any time in their busy day to feel calm and grounded.</p>
  </div>

  <div style="left:0;top:605px;width:199px;height:63px;background:#fbfafd"></div>
  <h2 class="script h-center" style="top:613px;font-size:8.5px">Subscribe to the Newsletter</h2>
  <p class="txt" style="left:44px;width:111px;top:628px;text-align:center">Lorem ipsum dolor sit amet, consectetur adipiscing elit, sed do eiusmod tempor incididunt ut labore et dolore magna aliqua ipsum suspendisse ultr.</p>
  <div style="left:50px;top:645px;width:72px;height:8px;border-radius:4px;background:#f0eff3;font-size:2px;color:#aaa;padding:2.5px 3px">Email</div>
  <a class="pill" style="left:122px;top:645px;font-size:2.6px;padding:2px 4px">Subscribe</a>

  <footer class="footer" style="top:668px;height:61px">
    <h4 class="f-title" style="left:22px">Contact Us</h4>
    <div class="f-lines" style="left:22px"><p>👤 Contact: Rachel Donovan</p><p>☎ Phone: 0400 555 218</p><p>✉ Email: info@openharboryoga.com.au</p><p>⌖ Location: Elmbrook, Victoria Australia 3999</p></div>
    <div class="f-logo"><span class="brand-dot"></span><span class="brand-name">OpenHarbor Yoga</span></div>
    <h4 class="f-title" style="left:123px">Connect With Us</h4>
    <div class="f-lines" style="left:123px"><p>Social: OpenHarbor Yoga</p><p>Photos: openharboryoga4kids</p><p style="margin-top:1.5px">ABN: 12 345 678 901</p></div>
    <div class="f-rule"></div><p class="f-copy">Copyright 2023 OpenHarbor Yoga</p>
  </footer>
</section>

<!-- CLASSES -->
<section class="page" style="left:299px;top:55px;height:1056px">
  <div class="topbar"><span>✉ info@openharboryoga.com.au</span><span>☎ Call Us 0400 555 218</span></div>
  <nav class="nav"><div class="brand"><span class="brand-dot"></span><span class="brand-name">OpenHarbor Yoga</span></div>
    <ul class="nav-links"><li>Home</li><li>About</li><li class="on">Classes</li><li>Blog</li><li>Contact</li></ul><a class="pill">Enquire Now</a></nav>
  <header class="hero short"><div class="hero-ring"></div><div class="hero-title">Yoga Classes...</div></header>

  <h2 class="script h-center" style="top:115px;font-size:8.5px">OpenHarbor Kids Yoga Classes...</h2>
  <p class="txt h-center" style="top:130px;padding:0 40px;color:#666">Does your child or teen get anxious? Would they benefit from activities that help to build resilience, without competition or pressure?</p>
  <p style="left:21px;top:153px;width:70px;font-size:2.8px;font-weight:700;color:var(--violet-deep);line-height:1.2">OpenHarbor Yoga offers a range of options of classes for kids and teens:</p>
  <ul class="ticks" style="left:21px;top:163px;width:72px"><li>after school classes (Day and Location)</li><li>day care/ early learning (age 2- preschool)</li><li>school (as part of the curriculum)</li><li>private sessions (in person at Location)</li></ul>
  <p style="left:21px;top:191px;width:70px;font-size:2.8px;font-weight:700;color:var(--teal-deep);line-height:1.2">Classes are a perfect blend of fun + calm and include:</p>
  <ul class="ticks" style="left:21px;top:201px;width:78px"><li>mindful movements</li><li>stretches to improve flexibility</li><li>exercises to help build strength, co-ordination &amp; good posture</li><li>fun group activities and games to enhance teamwork; social skills; playfulness &amp; conscious communication</li><li>calm breathing techniques</li><li>mindfulness activities</li><li>guided relaxation to reduce anxiety</li></ul>
  <p class="txt" style="left:21px;top:248px;width:70px">Classes are tailored to meet the unique needs of the group to be age appropriate and suitable for their capability.</p>
  <div class="bar" style="left:98px;top:158px;width:18px;height:30px"></div>
  <div class="ph cool" role="img" aria-label="Photo of a child in a tree pose" style="left:102px;top:161px;width:36px;height:37px"></div>
  <div class="ph" role="img" aria-label="Photo of a child stretching on a mat" style="left:141px;top:161px;width:37px;height:37px"></div>
  <div class="bar" style="left:160px;top:235px;width:21px;height:21px"></div>
  <div class="ph cool" role="img" aria-label="Photo of children stretching arms out in class" style="left:101px;top:202px;width:77px;height:51px"></div>

  <div style="left:0;top:275px;width:199px;height:185px;background:var(--grey-band)"></div>
  <div class="ph warm" role="img" aria-label="Photo of colourful wooden number blocks" style="left:21px;top:292px;width:80px;height:53px"></div>
  <h3 class="script" style="left:105px;top:293px;font-size:6px">Yoga in Early Learning ...</h3>
  <p style="left:105px;top:304px;width:75px;font-size:2.5px;font-weight:700;color:#333;line-height:1.3">Offer OpenHarbor Yoga at your childcare centre or Kindergarten!</p>
  <div class="txt" style="left:105px;top:314px;width:75px"><p>Give little ones a way to let out their energy in a healthy and mindful environment. OpenHarbor Yoga's experienced kids and teens yoga teacher teach children to have fun with yoga, build strength, focus, balance and coordination in a kind and nurturing way.</p><p>Yoga sessions can be tailored for the different ages of children, group size, curriculum strand / themes in the centre; weekly program, or one-off class. We bring yoga to you and Catering for the whole centre.</p></div>
  <ul class="ticks" style="left:105px;top:352px;width:75px"><li>15 min classes with ages 2-3</li><li>20 min class with ages 3-4</li><li>30 min class with ages 4-5</li></ul>
  <div style="left:105px;top:369px;width:70px;height:11px;background:linear-gradient(90deg,#6b3fc0,#1fb5d2);color:#fff;font-size:2.2px;font-weight:700;padding:2px 3px;line-height:1.25">Costs: from $90- $180 depending on location, duration, mats, class sizes</div>
  <h3 class="script" style="left:21px;top:378px;font-size:7px">Yoga in Schools...</h3>
  <p class="script" style="left:21px;top:389px;font-size:3.5px;color:#333">Offer OpenHarbor Yoga at your school!</p>
  <div class="txt" style="left:21px;top:397px;width:78px"><p>Classes are tailored by the age of students, group size, curriculum strand / mode relevant to a subject, term program or one-off class for both Primary and High Schools. We bring yoga to you, options include after school club, yoga as a PE unit, yoga in health class, and more.</p><p>Experienced kids and teens yoga teacher that engage kids with thoughtful yoga classes that develop strength, focus, confidence and more. Balanced with time to breathe and reset. Online Classes are also available.</p></div>
  <div style="left:21px;top:434px;width:70px;height:12px;background:var(--plum);color:#fff;font-size:2.2px;font-weight:700;padding:2.3px 3px;line-height:1.25">Costs: from $120- $200 depending on location, duration, mats, and class size.</div>
  <div class="ph green" role="img" aria-label="Photo of an apple on books with pencils before a chalkboard" style="left:104px;top:397px;width:74px;height:46px"></div>

  <div class="ph" role="img" aria-label="Photo of a person seated in meditation on a mat" style="left:20px;top:473px;width:79px;height:75px"></div>
  <h3 class="script" style="left:104px;top:474px;font-size:6px">Yoga for Tweens (aged 7-11)...</h3>
  <p class="txt" style="left:104px;top:484px;width:70px">An interactive 60-minute class for children aged 7-11 to enjoy yoga poses; games; partner yoga and learning life skills in a fun way. Each class ends with quiet time to breathe and relax.</p>
  <div style="left:104px;top:500px;font-size:2.5px;color:#333;line-height:1.35"><b>When:</b><br><span class="txt">Day &amp; Time<br>Term: Aug 20- Sept 7</span><br><b>Cost:</b><br><span style="font-size:2.1px">$55 4 class pass<br>$110 term pass<br>$170 term pass for 2 siblings<br>No credits for missed classes</span></div>
  <div style="left:140px;top:500px;font-size:2.5px;color:#333;line-height:1.35"><b>Where:</b><br><span class="txt">TBC</span></div>
  <a class="pill" style="left:104px;top:538px;background:var(--violet-deep)">Book Now</a>

  <div class="ph cool" role="img" aria-label="Photo of teen girls in a downward dog pose" style="left:20px;top:561px;width:79px;height:78px"></div>
  <h3 class="script" style="left:104px;top:562px;font-size:6px">Yoga for Teen Girls...</h3>
  <div class="txt" style="left:104px;top:572px;width:70px"><p>A beautiful class for teen girls to learn life skills and build self-confidence through yoga poses and empowering affirmations and partner yoga. Each class ends with quiet time to breathe and relax.</p><p>If your daughter is not yet a teen, but is in high school, she can join.</p></div>
  <div style="left:104px;top:597px;font-size:2.5px;color:#333;line-height:1.35"><b>When:</b><br><span class="txt">Thursday, 5-6pm<br>Term 3: July 20- Sept 7</span><br><b>Cost:</b><br><span style="font-size:2.1px">$60 4 class pass<br>$120 term pass<br>$190 term pass for 2 siblings<br>No credits for missed classes</span></div>
  <div style="left:140px;top:597px;font-size:2.5px;color:#333;line-height:1.35"><b>Where:</b><br><span class="txt">TBC</span></div>
  <a class="pill" style="left:104px;top:637px;background:var(--violet-deep)">Book Now</a>

  <div style="left:0;top:666px;width:199px;height:77px;background:linear-gradient(180deg,#6a3ea6,#3d86c4 60%,#22bcd6)"></div>
  <h2 class="script h-center" style="top:673px;font-size:7.5px;color:#fff">Private Sessions...</h2>
  <div class="txt h-center" style="top:688px;padding:0 40px;color:#fff"><p>If a group class is not suitable for your child, or if they would benefit from an individualised program to suit their needs, then you can consider a private lesson.</p><p>As a Kids Yoga Teacher, I have a Working with Children's Check card, first aid certificate, insurance, and relevant qualifications.</p><p>One on one, private sessions are the most effective way to ensure the student receives exactly what is right for them in the moment.</p></div>
  <a class="pill" style="left:86px;top:723px;border:0.6px solid #fff;background:transparent">Enquire Now</a>

  <div style="left:0;top:743px;width:199px;height:73px;background:var(--mist)"></div>
  <div class="ph cool" role="img" aria-label="Round photo of a child doing yoga at home in front of a laptop" style="left:43px;top:754px;width:52px;height:52px;border-radius:50%"></div>
  <h3 class="script" style="left:105px;top:765px;font-size:7px">Kids Yoga Online</h3>
  <p style="left:105px;top:777px;width:62px;font-size:3px;color:#666;line-height:1.35">"Online" is the new world we live in... So, if face to face sessions with me aren't possible, check out these options.</p>

  <h3 class="script" style="left:20px;top:833px;font-size:5.5px">Online private sessions for kids</h3>
  <p class="txt" style="left:20px;top:843px;width:70px">Online private sessions by video call are designed for kids who physically cannot make it to a yoga class, either due to distance, anxiety, or medical reasons. I will tailor the activities and duration (30-60 mins) to suit their individual needs.</p>
  <p style="left:20px;top:868px;width:72px;font-size:2.5px;font-weight:700;color:#333;line-height:1.3">Yes! I want my child to learn calm tools in a tailored, online private session</p>
  <a class="pill" style="left:20px;top:879px">Enquire Now</a>
  <div class="ph" role="img" aria-label="Photo of an adult and child in a side stretch pose" style="left:99px;top:832px;width:79px;height:52px"></div>

  <div class="ph green" role="img" aria-label="Photo of children on mats outdoors raising their arms" style="left:19px;top:902px;width:79px;height:67px"></div>
  <h3 class="script" style="left:106px;top:901px;font-size:5.5px">Online sessions for schools</h3>
  <p class="txt" style="left:106px;top:911px;width:70px">If you want to schedule in a little chill out time between lessons, or at the end of a structured day of learning, I will teach a class that is tailored to your group's age &amp; needs. They don't even need to look at the screen the whole time!</p>
  <p class="txt" style="left:106px;top:931px;width:60px">Options for:<br>- Preschool &amp; Prep<br>- Primary School<br>- High School</p>
  <p style="left:106px;top:951px;width:66px;font-size:2.5px;font-weight:700;color:#333;line-height:1.3">Yes! Our kids would benefit from some chill out time</p>
  <a class="pill" style="left:106px;top:962px;background:var(--plum)">Enquire Now</a>

  <footer class="footer" style="top:993px;height:63px">
    <h4 class="f-title" style="left:22px">Contact Us</h4>
    <div class="f-lines" style="left:22px"><p>👤 Contact: Rachel Donovan</p><p>☎ Phone: 0400 555 218</p><p>✉ Email: info@openharboryoga.com.au</p><p>⌖ Location: Elmbrook, Victoria Australia 3999</p></div>
    <div class="f-logo"><span class="brand-dot"></span><span class="brand-name">OpenHarbor Yoga</span></div>
    <h4 class="f-title" style="left:123px">Connect With Us</h4>
    <div class="f-lines" style="left:123px"><p>Social: OpenHarbor Yoga</p><p>Photos: openharboryoga4kids</p><p style="margin-top:1.5px">ABN: 12 345 678 901</p></div>
    <div class="f-rule"></div><p class="f-copy">Copyright 2023 OpenHarbor Yoga</p>
  </footer>
</section>

<!-- BLOG -->
<section class="page" style="left:539px;top:55px;height:616px">
  <div class="topbar"><span>✉ info@openharboryoga.com.au</span><span>☎ Call Us 0400 555 218</span></div>
  <nav class="nav"><div class="brand"><span class="brand-dot"></span><span class="brand-name">OpenHarbor Yoga</span></div>
    <ul class="nav-links"><li>Home</li><li>About</li><li>Classes</li><li class="on">Blog</li><li>Contact</li></ul><a class="pill">Enquire Now</a></nav>
  <header class="hero short"><div class="hero-ring"></div><div class="hero-title">OpenHarbor Yoga Blog</div></header>
  <div class="blog-bg" style="height:453px"></div>
  <h2 class="script" style="left:17px;top:117px;font-size:9px">Latest Blog Posts</h2>

  <article class="card" style="top:136px"><div class="thumb ph warm" role="img" aria-label="Blog thumbnail of a yoga class"></div><h3 class="c-title">Lorem ipsum dolor sit ame consectetur adipisciniore elised do eiusmod</h3><p class="c-meta">Aug 06, 2023 &nbsp; 💬 2 &nbsp; 👁 947</p><p class="c-text txt">Lorem ipsum dolor sit amet, consectetur adipiscing elit, sed do eiusmod tempor incididunt ut labore et dolore magna aliqua. Quis ipsum susp endisse ultrices gravidasus commodo viverra maecen.</p><div class="avatar"></div><p class="c-author">Admin by<b>Rachel Donovan</b></p><a class="pill">Continue Reading</a></article>
  <article class="card" style="top:213px"><div class="thumb ph" role="img" aria-label="Blog thumbnail of a stretching pose"></div><h3 class="c-title">Lorem ipsum dolor sit ame consectetur adipisciniore elised do eiusmod</h3><p class="c-meta">Aug 06, 2023 &nbsp; 💬 2 &nbsp; 👁 947</p><p class="c-text txt">Lorem ipsum dolor sit amet, consectetur adipiscing elit, sed do eiusmod tempor incididunt ut labore et dolore magna aliqua. Quis ipsum susp endisse ultrices gravidasus commodo viverra maecen.</p><div class="avatar"></div><p class="c-author">Admin by<b>Rachel Donovan</b></p><a class="pill">Continue Reading</a></article>
  <article class="card" style="top:291px"><div class="thumb ph cool" role="img" aria-label="Blog thumbnail of partner yoga"></div><h3 class="c-title">Lorem ipsum dolor sit ame consectetur adipisciniore elised do eiusmod</h3><p class="c-meta">Aug 06, 2023 &nbsp; 💬 2 &nbsp; 👁 947</p><p class="c-text txt">Lorem ipsum dolor sit amet, consectetur adipiscing elit, sed do eiusmod tempor incididunt ut labore et dolore magna aliqua. Quis ipsum susp endisse ultrices gravidasus commodo viverra maecen.</p><div class="avatar"></div><p class="c-author">Admin by<b>Rachel Donovan</b></p><a class="pill">Continue Reading</a></article>
  <article class="card" style="top:368px"><div class="thumb ph warm" role="img" aria-label="Blog thumbnail of a child balancing"></div><h3 class="c-title">Lorem ipsum dolor sit ame consectetur adipisciniore elised do eiusmod</h3><p class="c-meta">Aug 06, 2023 &nbsp; 💬 2 &nbsp; 👁 947</p><p class="c-text txt">Lorem ipsum dolor sit amet, consectetur adipiscing elit, sed do eiusmod tempor incididunt ut labore et dolore magna aliqua. Quis ipsum susp endisse ultrices gravidasus commodo viverra maecen.</p><div class="avatar"></div><p class="c-author">Admin by<b>Rachel Donovan</b></p><a class="pill">Continue Reading</a></article>
  <article class="card" style="top:445px"><div class="thumb ph green" role="img" aria-label="Blog thumbnail of a group class outdoors"></div><h3 class="c-title">Lorem ipsum dolor sit ame consectetur adipisciniore elised do eiusmod</h3><p class="c-meta">Aug 06, 2023 &nbsp; 💬 2 &nbsp; 👁 947</p><p class="c-text txt">Lorem ipsum dolor sit amet, consectetur adipiscing elit, sed do eiusmod tempor incididunt ut labore et dolore magna aliqua. Quis ipsum susp endisse ultrices gravidasus commodo viverra maecen.</p><div class="avatar"></div><p class="c-author">Admin by<b>Rachel Donovan</b></p><a class="pill">Continue Reading</a></article>

  <aside class="side" style="top:133px;height:190px">
    <h3 class="script" style="left:0;top:0;font-size:6px">Recent Posts</h3>
    <ul class="recent">
      <li style="top:14px"><div class="rt ph warm" role="img" aria-label="Recent post thumbnail"></div><p class="rx">Lorem ipsum dolor sit amet, consectetur loremadiisi<em>August 11, 2023</em></p></li>
      <li style="top:33px"><div class="rt ph" role="img" aria-label="Recent post thumbnail"></div><p class="rx">Lorem ipsum dolor sit amet, consectetur loremadiisi<em>August 11, 2023</em></p></li>
      <li style="top:52px"><div class="rt ph warm" role="img" aria-label="Recent post thumbnail"></div><p class="rx">Lorem ipsum dolor sit amet, consectetur loremadiisi<em>August 11, 2023</em></p></li>
      <li style="top:71px"><div class="rt ph cool" role="img" aria-label="Recent post thumbnail"></div><p class="rx">Lorem ipsum dolor sit amet, consectetur loremadiisi<em>August 11, 2023</em></p></li>
    </ul>
    <h3 class="script" style="left:0;top:102px;font-size:6px">Advertising</h3>
    <div class="ad ph cool" role="img" aria-label="Advert photo of smiling children holding yoga mats" style="top:116px"></div>
    <p class="ad-note" style="top:163px">Lorem ipsum dolor sit amet, consectetur adipiscing elit, sed do eiusmod temp</p>
  </aside>

  <p style="left:47px;top:531px;font-size:2.6px;color:#555">Page 1 of 3</p>
  <a class="pill" style="left:71px;top:529px;background:var(--teal-deep);font-size:2.6px;padding:1.6px 4px">Next</a>

  <footer class="footer" style="top:555px;height:61px">
    <h4 class="f-title" style="left:22px">Contact Us</h4>
    <div class="f-lines" style="left:22px"><p>👤 Contact: Rachel Donovan</p><p>☎ Phone: 0400 555 218</p><p>✉ Email: info@openharboryoga.com.au</p><p>⌖ Location: Elmbrook, Victoria Australia 3999</p></div>
    <div class="f-logo"><span class="brand-dot"></span><span class="brand-name">OpenHarbor Yoga</span></div>
    <h4 class="f-title" style="left:123px">Connect With Us</h4>
    <div class="f-lines" style="left:123px"><p>Social: OpenHarbor Yoga</p><p>Photos: openharboryoga4kids</p><p style="margin-top:1.5px">ABN: 12 345 678 901</p></div>
    <div class="f-rule"></div><p class="f-copy">Copyright 2023 OpenHarbor Yoga</p>
  </footer>
</section>

<!-- SINGLE BLOG -->
<section class="page" style="left:779px;top:55px;height:584px">
  <div class="topbar"><span>✉ info@openharboryoga.com.au</span><span>☎ Call Us 0400 555 218</span></div>
  <nav class="nav"><div class="brand"><span class="brand-dot"></span><span class="brand-name">OpenHarbor Yoga</span></div>
    <ul class="nav-links"><li>Home</li><li>About</li><li>Classes</li><li class="on">Blog</li><li>Contact</li></ul><a class="pill">Enquire Now</a></nav>
  <header class="hero short"><div class="hero-ring"></div><div class="hero-title">OpenHarbor Yoga Blog</div></header>
  <div class="blog-bg" style="height:421px"></div>

  <article style="left:19px;top:121px;width:105px;height:275px;background:#fff">
    <h2 style="position:absolute;left:5px;top:7px;width:95px;font-size:4.4px;font-weight:700;color:var(--violet-deep);line-height:1.15">Lorem ipsum dolor sit ametlol cons ectetur adipiscing elitlorem.</h2>
    <div class="ph" role="img" aria-label="Photo of people standing on yoga mats" style="position:absolute;left:5px;top:24px;width:94px;height:57px"></div>
    <p style="position:absolute;left:5px;top:84px;font-size:2px;color:#333">📅 Apr 30, 2023 &nbsp;·&nbsp; 1 min read &nbsp;&nbsp; 2 💬 &nbsp;&nbsp; 👁 947 &nbsp;&nbsp; 👤 Admin</p>
    <p class="txt" style="position:absolute;left:5px;top:91px;width:94px;font-size:2px">Lorem ipsum dolor sit amet,consec tetur adi piscing elit, sed do usmod tempor incidunt ut labore et dolore magna aliqua. Lorem ipsum dolor sit amet,consec tetur adi piscing elit, sed do usmod tempor incididunt ut labo ret dolore magna aliqua. Sed ut perspiciatis unde omnis iste natus error sit voluptatem accusantium doloremque laudantium, totam rem aperiam, eaque ipsa quae ab illo inventore veritatis et quasi architecto beatae vitae dicta sunt explicabo. Nemo enim ipsam voluptatem quia voluptas sit asp ernatur aut odit aut fugit, sed quia consequuntur magni dolores eos qui ratione voluptatem sequi nesciunt. Neque porro quisquam est, qui dolor em ipsum quia dolor sit amet, consectetur, adipisci velit, sed quia non numquam eius modi tempora incidunt ut labore et dolore magnam aliqu am quaerat voluptatem.</p>
    <div class="ph cool" role="img" aria-label="Photo of a smiling child stretching on a mat in class" style="position:absolute;left:5px;top:140px;width:94px;height:56px"></div>
    <h2 style="position:absolute;left:5px;top:202px;width:95px;font-size:4.4px;font-weight:700;color:var(--violet-deep);line-height:1.15">Lorem ipsum dolor sit ametlol cons ectetur adipiscing elitlorem.</h2>
    <p class="txt" style="position:absolute;left:5px;top:220px;width:94px;font-size:2px">Lorem ipsum dolor sit amet,consec tetur adi piscing elit, sed do usmod tem por incididunt ut labore et dolore magna aliqua. Lorem ipsum dolor sit amet consec tetur adi piscing elit, sed do usmod tempor incididunt ut labore et dolore magna aliqua. Sed ut perspiciatis unde omnis iste natus error sit voluptatem accusantium doloremque laudantium, totam rem aperiam, eaque ipsa quae ab illo inventore veritatis et quasi architecto beatae vitae dicta sunt explicabo. Nemo enim ipsam voluptatem quia voluptas sit asp ernatur aut odit aut fugit, sed quia consequuntur magni dolores eos q.</p>
    <div style="position:absolute;left:5px;right:5px;top:253px;height:0.4px;background:#ccc"></div>
    <p style="position:absolute;left:5px;top:260px;font-size:2.6px;color:#333">Share Article:</p>
    <div style="position:absolute;left:29px;top:258px;display:flex;gap:3px">
      <span style="width:7px;height:7px;border-radius:50%;background:#2f5bb8"></span><span style="width:7px;height:7px;border-radius:50%;background:#2f9ae6"></span><span style="width:7px;height:7px;border-radius:50%;background:#e0454a"></span><span style="width:7px;height:7px;border-radius:50%;background:#2fbf6a"></span>
    </div>
  </article>

  <form style="left:19px;top:405px;width:105px;height:110px;background:#fff">
    <p style="position:absolute;left:5px;top:10px;font-size:2.8px;font-weight:700;color:var(--violet-deep)">Leave a Reply</p>
    <div style="position:absolute;left:25px;right:6px;top:12px;height:0.4px;background:var(--teal)"></div>
    <div style="position:absolute;left:5px;top:19px;width:94px;height:23px;border:0.4px solid #ccc;font-size:1.8px;color:#999;padding:2px">Comment</div>
    <div style="position:absolute;left:5px;top:45px;width:50px;height:7px;border:0.4px solid #ccc;font-size:1.8px;color:#999;padding:2px">Name</div>
    <div style="position:absolute;left:55px;top:45px;width:44px;height:7px;border:0.4px solid #ccc;font-size:1.8px;color:#999;padding:2px">Email</div>
    <div style="position:absolute;left:5px;top:55px;width:94px;height:7px;border:0.4px solid #ccc;font-size:1.8px;color:#999;padding:2px">Website</div>
    <div style="position:absolute;left:5px;top:67px;width:3px;height:3px;border:0.4px solid #888"></div>
    <p style="position:absolute;left:10px;top:67px;font-size:1.6px;color:#777">Save my name, email, and website in this browser for the next time I comment.</p>
    <a class="pill" style="left:5px;top:76px;font-size:2.6px;padding:3px 8px">Post Comment</a>
  </form>

  <aside class="side" style="top:133px;height:190px">
    <h3 class="script" style="left:0;top:0;font-size:6px">Recent Posts</h3>
    <ul class="recent">
      <li style="top:14px"><div class="rt ph warm" role="img" aria-label="Recent post thumbnail"></div><p class="rx">Lorem ipsum dolor sit amet, consectetur loremadiisi<em>August 11, 2023</em></p></li>
      <li style="top:33px"><div class="rt ph" role="img" aria-label="Recent post thumbnail"></div><p class="rx">Lorem ipsum dolor sit amet, consectetur loremadiisi<em>August 11, 2023</em></p></li>
      <li style="top:52px"><div class="rt ph warm" role="img" aria-label="Recent post thumbnail"></div><p class="rx">Lorem ipsum dolor sit amet, consectetur loremadiisi<em>August 11, 2023</em></p></li>
      <li style="top:71px"><div class="rt ph cool" role="img" aria-label="Recent post thumbnail"></div><p class="rx">Lorem ipsum dolor sit amet, consectetur loremadiisi<em>August 11, 2023</em></p></li>
    </ul>
    <h3 class="script" style="left:0;top:102px;font-size:6px">Advertising</h3>
    <div class="ad ph cool" role="img" aria-label="Advert photo of smiling children holding yoga mats" style="top:116px"></div>
    <p class="ad-note" style="top:163px">Lorem ipsum dolor sit amet, consectetur adipiscing elit, sed do eiusmod temp</p>
  </aside>

  <footer class="footer" style="top:523px;height:61px">
    <h4 class="f-title" style="left:22px">Contact Us</h4>
    <div class="f-lines" style="left:22px"><p>👤 Contact: Rachel Donovan</p><p>☎ Phone: 0400 555 218</p><p>✉ Email: info@openharboryoga.com.au</p><p>⌖ Location: Elmbrook, Victoria Australia 3999</p></div>
    <div class="f-logo"><span class="brand-dot"></span><span class="brand-name">OpenHarbor Yoga</span></div>
    <h4 class="f-title" style="left:123px">Connect With Us</h4>
    <div class="f-lines" style="left:123px"><p>Social: OpenHarbor Yoga</p><p>Photos: openharboryoga4kids</p><p style="margin-top:1.5px">ABN: 12 345 678 901</p></div>
    <div class="f-rule"></div><p class="f-copy">Copyright 2023 OpenHarbor Yoga</p>
  </footer>
</section>

<!-- CONTACT -->
<section class="page" style="left:539px;top:718px;height:279px">
  <div class="topbar"><span>✉ info@openharboryoga.com.au</span><span>☎ Call Us 0400 555 218</span></div>
  <nav class="nav"><div class="brand"><span class="brand-dot"></span><span class="brand-name">OpenHarbor Yoga</span></div>
    <ul class="nav-links"><li>Home</li><li>About</li><li>Classes</li><li>Blog</li><li class="on">Contact</li></ul><a class="pill">Enquire Now</a></nav>
  <header class="hero" style="height:88px"><div class="hero-ring" style="top:6px;height:62px;width:62px;left:30px"></div><div class="hero-title" style="top:30px;font-size:12px">Contact</div></header>
  <form style="left:21px;top:100px;width:158px;height:111px;background:#fff">
    <h2 class="script" style="position:absolute;left:0;width:100%;text-align:center;top:11px;font-size:9px">Get In Touch</h2>
    <div style="position:absolute;left:12px;top:31px;width:64px;border-bottom:0.4px solid #ddd;font-size:2.3px;color:#555;padding-bottom:2px">Name:</div>
    <div style="position:absolute;left:81px;top:31px;width:64px;border-bottom:0.4px solid #ddd;font-size:2.3px;color:#555;padding-bottom:2px">Phone:</div>
    <div style="position:absolute;left:12px;top:43px;width:64px;border-bottom:0.4px solid #ddd;font-size:2.3px;color:#555;padding-bottom:2px">Email:</div>
    <div style="position:absolute;left:81px;top:43px;width:64px;border-bottom:0.4px solid #ddd;font-size:2.3px;color:#555;padding-bottom:2px">Subject:</div>
    <div style="position:absolute;left:12px;top:55px;width:133px;height:13px;border-bottom:0.4px solid #ddd;font-size:2.3px;color:#555">Message:</div>
    <a class="pill" style="left:64px;top:77px;background:linear-gradient(90deg,#6b3fc0,#1fb5d2);font-size:2.6px;padding:2px 5px">Submit Now</a>
  </form>
  <footer class="footer" style="top:211px;height:68px">
    <h4 class="f-title" style="left:22px">Contact Us</h4>
    <div class="f-lines" style="left:22px"><p>👤 Contact: Rachel Donovan</p><p>☎ Phone: 0400 555 218</p><p>✉ Email: info@openharboryoga.com.au</p><p>⌖ Location: Elmbrook, Victoria Australia 3999</p></div>
    <div class="f-logo"><span class="brand-dot"></span><span class="brand-name">OpenHarbor Yoga</span></div>
    <h4 class="f-title" style="left:123px">Connect With Us</h4>
    <div class="f-lines" style="left:123px"><p>Social: OpenHarbor Yoga</p><p>Photos: openharboryoga4kids</p><p style="margin-top:1.5px">ABN: 12 345 678 901</p></div>
    <div class="f-rule" style="top:46px"></div><p class="f-copy" style="top:54px">Copyright 2023 OpenHarbor Yoga</p>
  </footer>
</section>

</body>
</html>
```